Website Design for Kids

We need to redesign our site pobtrundle.net.
Current site was done long ago in Flash. We need to remove Flash and create a responsive site which can be viewed on phone, tablets as well as PC.
We are looking for a new fresh design. No elements from existing design need to be incorporated into new design.
The site is targeted for kids 7-12 years old.
Design should have attractive colors and it should be easy to navigate. It will be even better to provide one theme for boys and one for girls.
New site will have following features:
SHORT STORIES
Ability to display thumbnails of stories available. When user click a story it will play.
See http://pobtrundle.net/stories/index.asp to get an idea.
MOVIES
We have two moves, more to come. Users will be able to see thumbnails and watch trailers. To watch full movie they will be redirect to a Plonta page where they can pay and watch.
See http://pobtrundle.net/Movies/ to get an idea.
PICTURE STORIES
This will feature short stories. When a story is clicked it will start playing. The stories will have picture and text, possibly audio too.
See http://pobtrundle.net/stories/stories.asp to get an idea.
AUDIO STORIES
Audio stories recorded from kids or adults will be played. Optional photo of the person who recorded story will be displayed. User will have option to select a story by clicking thumbnail of stories.
VIDEO STORIES
Like audio stories, user will be able to scroll though thumbnails of stories and play one. Short video 1-3 mins will be played.
- I have upgraded budget and added a few more simple requirements. Need to decide soon so please submit your designs asap.
Number of Pages Required
5+ page
Look and feel

```html
<!DOCTYPE html>
<html lang="en">
<head>
<meta charset="utf-8">
<title>Pobtrundle – Stories, Movies and Games for Kids</title>
<link rel="stylesheet" href="https://fonts.googleapis.com/css2?family=Crimson+Pro:wght@500;600&family=Open+Sans:wght@400&family=Raleway:wght@500;600;800&display=swap">
<style>
  :root {
    --sky-top: #7cc8f4;
    --sky-mid: #c6e9fb;
    --meadow: #8fd63a;
    --meadow-light: #d9f3a8;
    --page-white: #ffffff;
    --nav-top: #3d95f5;
    --nav-bottom: #1f6fe2;
    --nav-divider: #5aa6f7;
    --orange: #f58a07;
    --green: #7cc417;
    --green-dark: #66a90d;
    --blue: #1f7fd8;
    --footer-top: #2f86ee;
    --footer-bottom: #1b58cf;
    --text-grey: #555555;
    --logo-purple: #5b2bb3;
  }
  * { box-sizing: border-box; margin: 0; padding: 0; }
  html, body { width: 1166px; height: 1200px; overflow: hidden; background: var(--page-white); }
  body { font-family: "Open Sans", Arial, sans-serif; color: var(--text-grey); }
  .canvas { position: relative; width: 1166px; height: 1200px; overflow: hidden; background: var(--page-white); }

  .scenery {
    position: absolute; left: 0; top: 0; width: 1166px; height: 560px;
    background:
      radial-gradient(ellipse 200px 120px at 580px 60px, rgba(255,255,255,.85), rgba(255,255,255,0) 70%),
      linear-gradient(180deg, var(--sky-top) 0%, var(--sky-mid) 18%, var(--meadow) 36%, var(--meadow-light) 62%, var(--page-white) 100%);
  }

  .brand {
    position: absolute; left: 0; top: 38px; width: 1166px; text-align: center;
    font-family: "Raleway", sans-serif; font-weight: 800; font-size: 34px;
    color: var(--logo-purple); letter-spacing: .5px;
  }

  .main-nav {
    position: absolute; left: 186px; top: 115px; width: 793px; height: 47px;
    background: linear-gradient(180deg, var(--nav-top), var(--nav-bottom));
    border-radius: 6px 6px 0 0; display: flex;
  }
  .main-nav a {
    font-family: "Crimson Pro", serif; font-weight: 600; font-size: 17px; color: #fff;
    text-decoration: none; display: flex; align-items: center; justify-content: center;
    border-right: 1px solid var(--nav-divider);
  }
  .main-nav a:last-child { border-right: none; }

  .hero {
    position: absolute; left: 186px; top: 162px; width: 793px; height: 346px;
    border: 3px solid #fff; border-top: none; border-radius: 0 0 6px 6px;
    background: linear-gradient(180deg, #f4f39a 0%, #9fd34a 30%, #4f9e2c 60%, #78c34a 85%, #4db3e6 100%);
    box-shadow: 0 3px 6px rgba(0,0,0,.18);
  }
  .hero-dots { position: absolute; left: 372px; bottom: 14px; display: flex; gap: 5px; }
  .hero-dots span { width: 11px; height: 11px; border-radius: 50%; background: #fff; }

  .feature-card {
    position: absolute; top: 524px; width: 260px; height: 283px;
    border: 3px solid; border-radius: 20px 20px 26px 26px / 20px 20px 18px 18px;
    background: #fff; text-align: center; box-shadow: 0 6px 6px -4px rgba(0,0,0,.12);
  }
  .feature-card .art { position: absolute; left: 9px; top: 9px; width: 236px; height: 125px; border-radius: 14px; }
  .feature-card h2 {
    position: absolute; left: 0; top: 150px; width: 100%;
    font-family: "Crimson Pro", serif; font-weight: 500; font-size: 22px; letter-spacing: .3px;
  }
  .feature-card p { position: absolute; left: 12px; top: 178px; width: 230px; font-size: 9.5px; line-height: 16.5px; }
  .feature-card .btn {
    position: absolute; left: 80px; top: 233px; width: 94px; height: 28px; border-radius: 14px;
    color: #fff; font-family: "Raleway", sans-serif; font-size: 12px; font-weight: 500;
    display: flex; align-items: center; justify-content: center; text-decoration: none;
  }
  .card-stories { left: 183px; border-color: var(--orange); }
  .card-stories h2 { color: var(--orange); }
  .card-stories .btn { background: var(--orange); }
  .card-stories .art { background: linear-gradient(180deg, #cfe7ec, #a8c47a 70%, #6d7b5a); }
  .card-movies { left: 452px; border-color: var(--green); }
  .card-movies h2 { color: var(--green-dark); }
  .card-movies .btn { background: var(--green); }
  .card-movies .art { background: linear-gradient(180deg, #9fd6f0, #7cc24a 55%, #8a6a3e); }
  .card-pictures { left: 722px; border-color: var(--blue); }
  .card-pictures h2 { color: var(--blue); }
  .card-pictures .btn { background: var(--blue); }
  .card-pictures .art { background: linear-gradient(180deg, #9ccf57, #e6f3fb 35%, #ffffff 70%, #f3c6d2); border: 1px solid #dde; }

  .showcase { position: absolute; top: 862px; width: 400px; }
  .showcase h3 { font-family: "Raleway", sans-serif; font-weight: 500; font-size: 21px; }
  .showcase .pager { position: absolute; top: 8px; right: 0; }
  .showcase-games { left: 184px; }
  .showcase-games h3 { color: var(--green); }
  .showcase-stories { left: 595px; }
  .showcase-stories h3 { color: var(--blue); }
  .showcase-games .pager { right: 26px; }
  .showcase-stories .pager { right: 2px; }

  .tile { position: absolute; top: 40px; width: 120px; text-align: center; }
  .tile .thumb { width: 118px; height: 109px; border-radius: 6px; border: 1px solid #ddd; }
  .tile h4 { margin-top: 14px; font-family: "Raleway", sans-serif; font-weight: 600; font-size: 13px; }
  .tile p { margin-top: 4px; font-size: 9.5px; white-space: nowrap; }
  .showcase-games h4 { color: var(--green); }
  .showcase-stories h4 { color: var(--blue); }

  .site-footer { position: absolute; left: 0; top: 1092px; width: 1166px; height: 108px; }
  .site-footer svg.wave { position: absolute; left: 0; top: 0; }
  .footer-links {
    position: absolute; left: 184px; top: 45px; display: flex; gap: 8px;
    font-family: "Raleway", sans-serif; font-size: 11px; font-weight: 500; color: #fff;
  }
  .footer-links a { color: #fff; text-decoration: none; }
  .copyright { position: absolute; left: 184px; top: 66px; font-size: 8.5px; color: #b9d4f7; }
  .social { position: absolute; left: 895px; top: 49px; display: flex; gap: 6px; }
  .social span { width: 20px; height: 20px; border-radius: 4px; background: #fff; }
</style>
</head>
<body>
<div class="canvas">
  <div class="scenery" role="img" aria-label="Cartoon meadow background with sky, clouds, butterflies, green hills and daisies"></div>

  <div class="brand">Pobtrundle</div>

  <nav class="main-nav">
    <a href="#" style="width:114px">Home</a>
    <a href="#" style="width:91px">About</a>
    <a href="#" style="width:91px">Games</a>
    <a href="#" style="width:95px">Stories</a>
    <a href="#" style="width:96px">Movies</a>
    <a href="#" style="width:113px">Activities</a>
    <a href="#" style="width:121px">Fund Stuff</a>
    <a href="#" style="width:72px">Shop</a>
  </nav>

  <section class="hero" role="img" aria-label="Illustrated forest clearing with a waterfall, deer, bear, fox, squirrel and birds">
    <div class="hero-dots"><span></span><span></span><span></span><span></span></div>
  </section>

  <article class="feature-card card-stories">
    <div class="art" role="img" aria-label="Illustration of two cartoon dragons"></div>
    <h2>SHORT STORIES</h2>
    <p>Morbi diam mauris viverra in gravida eu mattis in ante Morbi eget arcu Morbi porta libero id ullamcorper non-ummy nibh ligula pulvinar metus eget consecte</p>
    <a class="btn" href="#">View More</a>
  </article>
  <article class="feature-card card-movies">
    <div class="art" role="img" aria-label="Illustration of a fairy-tale landscape with mushroom houses and a river"></div>
    <h2>MOVIES</h2>
    <p>Morbi diam mauris viverra in gravida eu mattis in ante Morbi eget arcu Morbi porta libero id ullamcorper non-ummy nibh ligula pulvinar metus eget consecte</p>
    <a class="btn" href="#">View More</a>
  </article>
  <article class="feature-card card-pictures">
    <div class="art" role="img" aria-label="Illustration of a child in bunny ears under a tree"></div>
    <h2>PICTURE STORIES</h2>
    <p>Morbi diam mauris viverra in gravida eu mattis in ante Morbi eget arcu Morbi porta libero id ullamcorper non-ummy nibh ligula pulvinar metus eget consecte</p>
    <a class="btn" href="#">View More</a>
  </article>

  <section class="showcase showcase-games">
    <h3>Featured Games</h3>
    <svg class="pager" width="24" height="14" viewBox="0 0 24 14" fill="none" stroke="#999" stroke-width="1.5"><path d="M8 1 L2 7 L8 13"/><path d="M16 1 L22 7 L16 13"/></svg>
    <div class="tile" style="left:-1px"><div class="thumb" role="img" aria-label="Game illustration of a colourful market street" style="background:linear-gradient(180deg,#f2c14a,#c8432a 55%,#7a3b1e)"></div><h4>Tittle Name</h4><p>Morbi eget arcu Morbi porta</p></div>
    <div class="tile" style="left:127px"><div class="thumb" role="img" aria-label="Game illustration of a castle on green hills" style="background:linear-gradient(180deg,#a7d7ef,#7cc24a 55%,#4c8f2d)"></div><h4>Tittle Name</h4><p>Morbi eget arcu Morbi porta</p></div>
    <div class="tile" style="left:254px"><div class="thumb" role="img" aria-label="Game illustration of a forest treehouse" style="background:linear-gradient(180deg,#6b4a2a,#3f6a2c 55%,#2c3b1e)"></div><h4>Tittle Name</h4><p>Morbi eget arcu Morbi porta</p></div>
  </section>

  <section class="showcase showcase-stories">
    <h3>Featured Stories</h3>
    <svg class="pager" width="24" height="14" viewBox="0 0 24 14" fill="none" stroke="#999" stroke-width="1.5"><path d="M8 1 L2 7 L8 13"/><path d="M16 1 L22 7 L16 13"/></svg>
    <div class="tile" style="left:-1px"><div class="thumb" role="img" aria-label="Story illustration of a golden castle" style="background:linear-gradient(180deg,#d8eefa,#f1c43c 55%,#c99a1f)"></div><h4>Tittle Name</h4><p>Morbi eget arcu Morbi porta</p></div>
    <div class="tile" style="left:127px"><div class="thumb" role="img" aria-label="Story illustration of a playful fantasy scene" style="background:linear-gradient(180deg,#f6b8c8,#c99ad8 55%,#6b78c8)"></div><h4>Tittle Name</h4><p>Morbi eget arcu Morbi porta</p></div>
    <div class="tile" style="left:254px"><div class="thumb" role="img" aria-label="Story illustration of a fox in the countryside" style="background:linear-gradient(180deg,#f4e6a8,#c9a24a 55%,#8a6a3a)"></div><h4>Tittle Name</h4><p>Morbi eget arcu Morbi porta</p></div>
  </section>

  <footer class="site-footer">
    <svg class="wave" width="1166" height="108" viewBox="0 0 1166 108" preserveAspectRatio="none">
      <defs><linearGradient id="footerFill" x1="0" y1="0" x2="0" y2="1"><stop offset="0" stop-color="#2f86ee"/><stop offset="1" stop-color="#1b58cf"/></linearGradient></defs>
      <path d="M0 22 C 300 2, 700 2, 1166 14 L1166 108 L0 108 Z" fill="url(#footerFill)"/>
    </svg>
    <nav class="footer-links">
      <a href="#">HOME</a><span>|</span><a href="#">ABOUT US</a><span>|</span><a href="#">GAMES</a><span>|</span><a href="#">STOREIS</a><span>|</span><a href="#">ACTIVITIES</a><span>|</span><a href="#">FUN STUFF</a><span>|</span><a href="#">SHOP</a>
    </nav>
    <p class="copyright">© 2015 Company Name &nbsp;All right reserved &nbsp;Term of Use</p>
    <div class="social" aria-label="Social links"><span></span><span></span><span></span></div>
  </footer>
</div>
</body>
</html>
```